Mortgage Company ready to make a statement!

We have a basic logo that I am fairly happy with ... but it could use a little bit of tweaking before we order the sign for our building. We also want some knock-your-socks-off business cards.
Problem: Inside of our Mortgage Office (Bright Fern Mortgage Group), we are going to have a coffee lounge (Sunbrew Cafe) for Realtors to use instead of the local Cuppington to meet with homebuyers. The office and coffee lounge are in an industrial building and is decorated with cozy overstuffed chairs, a hodge podge of interesting lamps and furniture, and goal is to make it as inviting as possible. However, we are a financial institution... so we need to keep it pretty clean as well.
One of my favorite marketing ideas is to cut a house key for everyone who buys a home using us with a key that matches our logo. There's only one key shape that works really well, so that needs to match the logo in order for the idea to work. I'll attach an image of the key blank.... although the way the key hole cut out looks terrible, so I was thinking of having them just do a thin outline instead.
Would like a similar, matching logo for the Sunbrew Cafe... but possibly something that would be a little less formal and would be cute on a coffee mug- nothing stuffy.
AND, we're opening a home inspection company as well, and we would like that logo and branding to match. The home inspection company is "Bright Fern Home Inspections"
We were thinking that for the home inspection company , we could use a magnifying glass shape inside of the house shape for the logo, use a keyhole shape inside of the same house for the mortgage company, and use a coffee cup inside of the house shape for Sunbrew Cafe.
Just getting stuck and need to help. I designed the attached logo myself, and that is what we are currently using. Designers at local printing companies have failed to impress us.
The mortgage industry has a lot of numbers and logos, etc that they require us to put on our business cards... so it's hard to keep them looking clean.
HELP! HELP! :)

```html
<!DOCTYPE html>
<html lang="en">
<head>
<meta charset="utf-8">
<title>Bright Fern Mortgage Group – Business Card</title>
<link rel="stylesheet" href="https://fonts.googleapis.com/css2?family=Marcellus&family=Montserrat:wght@400;600&display=swap">
<style>
  :root {
    --page-bg: #1c1c1e;
    --card-bg: #1f1f21;
    --card-edge: #2c2c2f;
    --brand-blue: #2f6f93;
    --front-grey: #8d8f94;
    --text-light: #e6e7e9;
    --icon-blue: #2f6f93;
  }
  * { margin: 0; padding: 0; box-sizing: border-box; }
  html, body {
    width: 1200px; height: 900px; overflow: hidden;
    background: var(--page-bg);
  }
  .canvas {
    width: 1200px; height: 900px;
    display: flex; flex-direction: column; align-items: center; justify-content: center;
    gap: 40px;
  }
  .card {
    width: 700px; height: 400px;
    background: var(--card-bg);
    border: 1px solid var(--card-edge);
    box-shadow: 0 14px 30px rgba(0,0,0,.45);
    position: relative;
  }
  .card-front {
    display: flex; align-items: center; justify-content: center;
  }
  .brand-name {
    font-family: "Montserrat", sans-serif;
    font-weight: 400;
    text-transform: none;
    line-height: 1.15;
    display: flex; align-items: center; gap: 14px;
  }
  .brand-mark {
    width: 14px; height: 14px; flex: none;
  }
  .card-front .brand-name { color: var(--front-grey); font-size: 40px; }
  .card-front .brand-mark { background: var(--front-grey); }

  .card-back {
    display: flex; align-items: center;
    padding: 0 50px 0 60px;
  }
  .card-back .brand-name {
    color: var(--brand-blue); font-size: 34px; width: 300px;
  }
  .card-back .brand-mark { background: var(--brand-blue); }
  .divider {
    width: 2px; height: 210px; background: var(--brand-blue);
    margin: 0 30px 0 20px;
  }
  .contact { color: var(--text-light); font-family: "Montserrat", sans-serif; }
  .person-name {
    font-family: "Marcellus", serif; color: var(--brand-blue);
    font-size: 26px; letter-spacing: 2px; text-transform: uppercase;
  }
  .person-title { font-weight: 600; font-size: 17px; letter-spacing: 1px; margin: 2px 0 18px; }
  .address { font-size: 15px; letter-spacing: 1px; line-height: 1.35; margin-bottom: 14px; }
  .contact-list { list-style: none; font-size: 15px; letter-spacing: 1px; }
  .contact-list li { display: flex; align-items: center; gap: 12px; line-height: 1.7; }
  .contact-list svg { width: 14px; height: 14px; flex: none; }
</style>
</head>
<body>
<main class="canvas">
  <section class="card card-front">
    <div class="brand-name"><span class="brand-mark"></span>Bright Fern Mortgage Group</div>
  </section>

  <section class="card card-back">
    <div class="brand-name"><span class="brand-mark"></span><span>Bright Fern<br>Mortgage Group</span></div>
    <div class="divider"></div>
    <div class="contact">
      <h1 class="person-name">Daniel Marsh</h1>
      <p class="person-title">CEO</p>
      <p class="address">Lantern Court<br>Sydney Melbourne</p>
      <ul class="contact-list">
        <li>
          <svg viewBox="0 0 14 14" aria-hidden="true"><rect x="3.5" y="1" width="7" height="12" rx="1.2" fill="none" stroke="var(--icon-blue)" stroke-width="1.3"/><circle cx="7" cy="11" r=".8" fill="var(--icon-blue)"/></svg>
          000-555-0142
        </li>
        <li>
          <svg viewBox="0 0 14 14" aria-hidden="true"><rect x="4" y="1" width="6" height="4" fill="var(--icon-blue)"/><rect x="1" y="5" width="12" height="5" rx="1" fill="var(--icon-blue)"/><rect x="4" y="9" width="6" height="4" fill="var(--icon-blue)"/></svg>
          000-555-0142
        </li>
        <li>
          <svg viewBox="0 0 14 14" aria-hidden="true"><rect x="1" y="3" width="12" height="8" fill="var(--icon-blue)"/><path d="M1 3 L7 8 L13 3" fill="none" stroke="var(--card-bg)" stroke-width="1"/></svg>
          daniel.marsh@brightfernmg.com
        </li>
      </ul>
    </div>
  </section>
</main>
</body>
</html>
```